House-share and Room Rental Website (With Focus on the Bedroom Landing Page)

Looking for website design for our House-share (executive accommodation) and room rental business.

Our company name is: Lodgivo could also be written as LodGivo or lodgivo. Either is fine .. just looking for a nice clean catchy logo to go with the design.

EXAMPLES
These are examples of other websites in this field that are doing well. this is a kind of baseline.
https://nestpartners-example.com.au/
https://www.bunkora-example.com/
https://www.dwelzy-example.com/
https://www.habiquo-example.net/
https://www.cohabiscout-example.com.au/

Our business model is to rent rooms to people looking for high-quality accommodation. We fill the gap between those looking to rent rooms and those with rooms to rent. However, our model is slightly different from those already on the market as we looking to fill a massive gap in the market delivering upmarket rooms for rent.(Executive Accommodation) also in the back end will be coupled with a self management process in the back end.

We offer executive style accommodation that stands out above the rest. With special extras like fire safety.. and management processes that create happier homes. We are looking for a web design package that can help us grow and scale our business. We need a design that is captivating

Our MAIN focus is having a room landing page that stands out from the rest... The core of our business will rely on the promotion of the rooms in a share house... so the whole design relies on the BEDROOM landing page to drive results.

Target Market(s)

We have 2 markets we are aiming at ... the first market is people offering rooms to rent who want the highest rental return. The second market is people looking to rent safe, high-quality rooms, in houses that are well managed and looked after.

Industry/Entity Type

Share Economy

Logo Text

LodGivo

Number of Pages Required

5+ page

Font styles to use
Sans Serif

Colors
3276b5

Requirements
Must have
• A messaging system whereby we can create direct communication between those offering rooms and those looking for rooms.
• A call to action that says " Schedule an Inspection"
• Landing page for promoting rooms
• A home page for showing stock.
• Profile page for those selling rooms
• Profile page for those looking for rooms.
• A scheduling calendar for booking inspections
Nice to have
• Pages where new residents can lock in a room.. pay bond and rents.. and sign contracts
• Notifications
• SMS capabilities in the backend.
Should not have
• No script or handwriting fonts.

```html
<!DOCTYPE html>
<html lang="en">
<head>
<meta charset="utf-8">
<title>Lodgivo – Executive Accommodation</title>
<link rel="stylesheet" href="https://fonts.googleapis.com/css2?family=Outfit:wght@300;400;500;600;700&display=swap">
<style>
:root{
  --blue:#3276b5;
  --blue-dark:#245a8c;
  --orange:#f39a2c;
  --ink:#1c1c1e;
  --text:#555a61;
  --muted:#8a8f96;
  --line:#d5d8dc;
  --pale:#f1f3f6;
  --footer:#262324;
  --footer-field:#4b4849;
  --white:#ffffff;
}
*{box-sizing:border-box;margin:0;padding:0}
html,body{width:1200px;height:3169px;overflow:hidden}
body{font-family:"Outfit",Arial,sans-serif;color:var(--ink);background:var(--white);position:relative}
a{color:inherit;text-decoration:none}
.btn-outline{display:inline-flex;align-items:center;justify-content:center;border:1.5px solid var(--blue);color:var(--blue);font-size:13px;border-radius:3px;background:var(--white)}

/* header */
.site-header{position:absolute;left:0;top:0;width:1200px;height:80px;background:var(--white)}
.brand{position:absolute;left:87px;top:14px}
.brand-name{font-size:27px;font-weight:600;color:var(--blue);display:flex;align-items:center;gap:8px;line-height:1}
.brand-square{width:16px;height:16px;background:var(--blue);border-radius:2px}
.brand-tag{font-size:11px;color:var(--muted);margin-top:6px;letter-spacing:.2px}
.main-nav a{position:absolute;top:30px;font-size:14px;color:var(--text)}
.main-nav a.active{color:var(--blue)}
.header-cta{position:absolute;left:928px;top:23px;width:183px;height:32px}

/* hero */
.hero{position:absolute;left:0;top:80px;width:1200px;height:440px;background:linear-gradient(180deg,#8fa6bd 0%,#5f6e7f 45%,#46505a 75%,#6d6a5f 100%)}
.hero-shade{position:absolute;inset:0;background:linear-gradient(90deg,rgba(40,70,40,.45),rgba(0,0,0,.05) 30%,rgba(0,0,0,.05) 70%,rgba(40,70,40,.45))}
.hero-title{position:absolute;left:0;width:1200px;top:128px;text-align:center;color:var(--white);font-size:44px;font-weight:600}
.hero-points{position:absolute;left:0;width:1200px;top:194px;display:flex;justify-content:center;gap:30px;color:var(--white);font-size:15px}
.hero-points span{display:flex;align-items:center;gap:8px}
.search{position:absolute;left:285px;top:254px;width:628px;height:42px;display:flex;background:var(--white);border-radius:2px}
.search-input{flex:1;padding-left:14px;font-size:13px;color:var(--muted);display:flex;align-items:center}
.search-btn{width:121px;background:var(--orange);color:var(--white);font-size:13px;display:flex;align-items:center;justify-content:center;gap:6px}

/* intro */
.intro{position:absolute;left:0;top:520px;width:1200px;height:380px;text-align:center}
.intro-logo{position:absolute;left:0;width:1200px;top:120px;display:flex;justify-content:center;align-items:center;gap:12px;font-size:44px;font-weight:500;color:var(--ink)}
.intro-logo .brand-square{width:26px;height:26px}
.intro-text{position:absolute;left:240px;width:720px;top:190px;font-size:14px;line-height:22px;color:var(--muted)}
.intro-btn{position:absolute;left:536px;top:268px;width:128px;height:32px}

/* audiences */
.audiences{position:absolute;left:0;top:900px;width:1200px;height:560px;background:var(--blue);color:var(--white)}
.section-title{position:absolute;left:0;width:1200px;text-align:center;font-size:38px;font-weight:600}
.audience{position:absolute;top:142px;width:290px;text-align:center}
.audience-photo{width:158px;height:158px;border-radius:50%;margin:0 auto;border:4px solid rgba(255,255,255,.9)}
.audience h3{font-size:18px;font-weight:500;margin-top:26px}
.audience p{font-size:13px;line-height:20px;margin:18px auto 0;width:250px;color:#e6eef7}
.audience .btn{margin-top:28px;display:inline-flex;align-items:center;justify-content:center;height:32px;width:128px;font-size:12px;border:1.5px solid var(--white);color:var(--white);border-radius:3px}
.audience .btn.solid{background:var(--white);color:var(--blue)}
.audience .btn.plain{border-color:transparent}

/* rooms */
.rooms{position:absolute;left:0;top:1460px;width:1200px;height:579px}
.rooms .section-title{top:72px;color:var(--ink)}
.accent{color:var(--blue)}
.tabs{position:absolute;top:138px;left:203px;display:flex;gap:20px}
.tab{width:186px;text-align:center;font-size:12px;color:var(--muted);padding-bottom:6px;border-bottom:2px solid var(--line)}
.tab.active{color:var(--orange);border-color:var(--orange)}
.room{position:absolute;top:199px;width:232px}
.room-photo{height:158px;position:relative}
.room-badge{position:absolute;right:0;bottom:0;background:var(--blue-dark);color:var(--white);font-size:11px;padding:4px 12px}
.room-price{font-size:15px;font-weight:600;color:var(--orange);margin-top:20px}
.room-loc{font-size:12px;color:var(--muted);margin-top:8px;display:flex;align-items:center;gap:6px}
.rooms-btn{position:absolute;left:503px;top:467px;width:194px;height:32px}

/* why */
.why{position:absolute;left:0;top:2039px;width:1200px;height:397px;background:linear-gradient(135deg,#eef1f5,#f6f7f9 45%,#e8ecf1)}
.why .section-title{top:58px;color:var(--ink)}
.why-item{position:absolute;top:146px;width:300px;text-align:center}
.why-item svg{display:block;margin:0 auto}
.why-item h3{font-size:17px;font-weight:400;margin-top:24px;color:var(--ink)}
.why-btn{position:absolute;left:508px;top:287px;width:184px;height:32px;background:var(--blue);color:var(--white);font-size:13px;display:flex;align-items:center;justify-content:center;border-radius:2px}

/* move */
.move{position:absolute;left:0;top:2436px;width:1200px;height:285px;text-align:center}
.move .section-title{top:76px;color:var(--ink)}
.move-sub{position:absolute;left:0;width:1200px;top:126px;font-size:15px;color:var(--text)}
.move-btn{position:absolute;left:524px;top:171px;width:152px;height:32px}

/* footer */
.site-footer{position:absolute;left:0;top:2721px;width:1200px;height:448px;background:var(--footer);color:#c9c7c8}
.footer-col{position:absolute;top:80px}
.footer-col h4{font-size:17px;font-weight:500;color:var(--white);margin-bottom:16px}
.phone{font-size:22px;color:var(--white);font-weight:300}
.small{font-size:13px;line-height:18px}
.directions{color:var(--blue);text-decoration:underline;font-size:13px;display:inline-block;margin-top:14px}
.socials{position:absolute;left:87px;top:302px;display:flex;gap:10px}
.social{width:30px;height:30px;border:1px solid var(--blue)}
.social.active{background:var(--blue)}
.links a{display:block;font-size:13px;line-height:29px}
.links a.active{color:var(--blue)}
.field{position:absolute;background:var(--footer-field);font-size:12px;color:#b5b2b3;padding:10px 12px}
.send{position:absolute;left:615px;top:305px;width:97px;height:31px;background:var(--blue);color:var(--white);font-size:13px;display:flex;align-items:center;justify-content:center;gap:8px}
.copyright{position:absolute;left:87px;top:384px;font-size:13px}
.to-top{position:absolute;left:1093px;top:378px}
</style>
</head>
<body>

<header class="site-header">
  <div class="brand">
    <div class="brand-name"><span class="brand-square"></span>Lodgivo</div>
    <div class="brand-tag">Executive Accommodation</div>
  </div>
  <nav class="main-nav">
    <a class="active" style="left:450px" href="#">Home</a>
    <a style="left:528px" href="#">About Us</a>
    <a style="left:628px" href="#">Services</a>
    <a style="left:723px" href="#">Portfolio</a>
    <a style="left:820px" href="#">Contact Us</a>
  </nav>
  <a class="btn-outline header-cta" href="#">Schedule an Inspection</a>
</header>

<section class="hero" role="img" aria-label="Photograph of a modern two-storey grey house with garage, surrounded by tall trees">
  <div class="hero-shade"></div>
  <h1 class="hero-title">Easiest Way to Rent a Home</h1>
  <div class="hero-points">
    <span><svg width="14" height="12" viewBox="0 0 14 12"><path d="M1 6l4 4 8-9" fill="none" stroke="#f39a2c" stroke-width="2"/></svg>Exclusive Homes</span>
    <span><svg width="14" height="12" viewBox="0 0 14 12"><path d="M1 6l4 4 8-9" fill="none" stroke="#f39a2c" stroke-width="2"/></svg>Assisted Visits</span>
    <span><svg width="14" height="12" viewBox="0 0 14 12"><path d="M1 6l4 4 8-9" fill="none" stroke="#f39a2c" stroke-width="2"/></svg>Instant Move-In</span>
  </div>
  <div class="search">
    <div class="search-input">Enter Locations / Landmark</div>
    <div class="search-btn"><svg width="12" height="12" viewBox="0 0 12 12"><circle cx="5" cy="5" r="3.6" fill="none" stroke="#fff" stroke-width="1.6"/><path d="M7.7 7.7L11 11" stroke="#fff" stroke-width="1.6"/></svg>Search</div>
  </div>
</section>

<section class="intro">
  <div class="intro-logo"><span class="brand-square"></span>Lodgivo</div>
  <p class="intro-text">Contrary to popular belief, Lorem Ipsum is not simply random text. It has roots in a piece of classical Latin literature from 45 BC, making it over 2000 years old. A Latin scholar at a small regional college in the valley, looked up one of the more obscure Latin words ...</p>
  <a class="btn-outline intro-btn" href="#">Discover More</a>
</section>

<section class="audiences">
  <h2 class="section-title" style="top:64px">Designed for Everyone</h2>
  <div class="audience" style="left:103px">
    <div class="audience-photo" role="img" aria-label="Photo of a shared bedroom with two beds" style="background:radial-gradient(circle at 40% 40%,#e7b57a,#a86a3a 60%,#5e3a22)"></div>
    <h3>Shared Rooms</h3>
    <p>Contrary to popular belief, Lorem Ipsum is not simply random text. It has roots in a piece of lorem ...</p>
    <a class="btn" href="#">Explore Rooms</a>
  </div>
  <div class="audience" style="left:455px">
    <div class="audience-photo" role="img" aria-label="Photo of a private bedroom with a green bed" style="background:radial-gradient(circle at 45% 55%,#cfd8b0,#c4735a 55%,#7c4b3d)"></div>
    <h3>Private Rooms</h3>
    <p>Contrary to popular belief, Lorem Ipsum is not simply random text. It has roots in a piece of lorem ...</p>
    <a class="btn solid" href="#">Explore Rooms</a>
  </div>
  <div class="audience" style="left:807px">
    <div class="audience-photo" role="img" aria-label="Photo of a full modern house" style="background:linear-gradient(180deg,#9fb8d2,#5c6670 55%,#4f5a3f)"></div>
    <h3>Full House</h3>
    <p>Contrary to popular belief, Lorem Ipsum is not simply random text. It has roots in a piece of lorem ...</p>
    <a class="btn plain" href="#">Explore House</a>
  </div>
</section>

<section class="rooms">
  <h2 class="section-title">Available <span class="accent">Rooms</span></h2>
  <div class="tabs">
    <div class="tab">All</div>
    <div class="tab active">Shared Rooms</div>
    <div class="tab">Private Rooms</div>
    <div class="tab">Full House</div>
  </div>

  <article class="room" style="left:87px">
    <div class="room-photo" role="img" aria-label="Photo of a shared bedroom with two beds" style="background:linear-gradient(135deg,#d9a36a,#8c5a36 60%,#4e3020)"><span class="room-badge">6 Rooms</span></div>
    <div class="room-price">$ 1,090 - $ 1,490</div>
    <div class="room-loc"><svg width="9" height="12" viewBox="0 0 9 12"><path d="M4.5 0A4.5 4.5 0 0 0 0 4.5C0 8 4.5 12 4.5 12S9 8 9 4.5A4.5 4.5 0 0 0 4.5 0z" fill="#3276b5"/><circle cx="4.5" cy="4.5" r="1.6" fill="#fff"/></svg>Corvel House - Bayview</div>
  </article>
  <article class="room" style="left:351px">
    <div class="room-photo" role="img" aria-label="Photo of a bedroom with twin beds and bright window" style="background:linear-gradient(135deg,#e8d2b0,#b07a4a 55%,#6e4a30)"><span class="room-badge">4 Rooms</span></div>
    <div class="room-price">$ 1,090 - $ 1,490</div>
    <div class="room-loc"><svg width="9" height="12" viewBox="0 0 9 12"><path d="M4.5 0A4.5 4.5 0 0 0 0 4.5C0 8 4.5 12 4.5 12S9 8 9 4.5A4.5 4.5 0 0 0 4.5 0z" fill="#3276b5"/><circle cx="4.5" cy="4.5" r="1.6" fill="#fff"/></svg>Corvel House - Bayview</div>
  </article>
  <article class="room" style="left:615px">
    <div class="room-photo" role="img" aria-label="Photo of a hotel-style room with two white beds" style="background:linear-gradient(135deg,#c9b9a4,#8e7a66 55%,#5a4a3c)"><span class="room-badge">5 Rooms</span></div>
    <div class="room-price">$ 1,090 - $ 1,490</div>
    <div class="room-loc"><svg width="9" height="12" viewBox="0 0 9 12"><path d="M4.5 0A4.5 4.5 0 0 0 0 4.5C0 8 4.5 12 4.5 12S9 8 9 4.5A4.5 4.5 0 0 0 4.5 0z" fill="#3276b5"/><circle cx="4.5" cy="4.5" r="1.6" fill="#fff"/></svg>Corvel House - Bayview</div>
  </article>
  <article class="room" style="left:879px">
    <div class="room-photo" role="img" aria-label="Photo of a bright bedroom with twin beds and red covers" style="background:linear-gradient(135deg,#efe6da,#c9a890 55%,#8a3d3a)"><span class="room-badge">6 Rooms</span></div>
    <div class="room-price">$ 1,090 - $ 1,490</div>
    <div class="room-loc"><svg width="9" height="12" viewBox="0 0 9 12"><path d="M4.5 0A4.5 4.5 0 0 0 0 4.5C0 8 4.5 12 4.5 12S9 8 9 4.5A4.5 4.5 0 0 0 4.5 0z" fill="#3276b5"/><circle cx="4.5" cy="4.5" r="1.6" fill="#fff"/></svg>Corvel House - Bayview</div>
  </article>

  <a class="btn-outline rooms-btn" href="#">View All Available Rooms</a>
</section>

<section class="why" role="img" aria-label="Faint background photo of a bright living room interior">
  <h2 class="section-title">Why <span class="accent">Choose Us</span></h2>
  <div class="why-item" style="left:98px">
    <svg width="60" height="62" viewBox="0 0 60 62"><path d="M38 16c-3-4-14-5-16 1-3 9 20 8 17 19-2 7-14 7-19 1" fill="none" stroke="#1c1c1e" stroke-width="2.6"/><path d="M30 6v52" stroke="#1c1c1e" stroke-width="2.6"/><path d="M8 56L54 8" stroke="#3276b5" stroke-width="2.6"/></svg>
    <h3>Zero Brokerage</h3>
  </div>
  <div class="why-item" style="left:454px">
    <svg width="66" height="62" viewBox="0 0 66 62"><circle cx="36" cy="14" r="11" fill="none" stroke="#3276b5" stroke-width="2.2"/><text x="36" y="19" text-anchor="middle" font-size="14" fill="#3276b5" font-family="Outfit,Arial,sans-serif">$</text><path d="M4 38h10v20H4zM14 42c8-4 14-4 20 0h10c4 0 4 6 0 6H32M14 54c10 3 18 4 28-2l18-11c3-2 0-7-4-5L44 42" fill="none" stroke="#1c1c1e" stroke-width="2.4" stroke-linejoin="round"/></svg>
    <h3>Affordable&nbsp; Rents</h3>
  </div>
  <div class="why-item" style="left:802px">
    <svg width="62" height="62" viewBox="0 0 62 62"><rect x="14" y="6" width="34" height="42" rx="3" transform="rotate(35 31 27)" fill="none" stroke="#1c1c1e" stroke-width="2.4"/><path d="M6 40l20 16 30-20" fill="none" stroke="#1c1c1e" stroke-width="2.4"/><path d="M22 22l18-12" stroke="#3276b5" stroke-width="2.4"/></svg>
    <h3>Low Security&nbsp; Deposits</h3>
  </div>
  <a class="why-btn" href="#">Schedule an Inspection</a>
</section>

<section class="move">
  <h2 class="section-title">Make Your <span class="accent">Move!</span></h2>
  <p class="move-sub">Create your <span class="accent">Lodgivo</span> account and join the largest flatshare community</p>
  <a class="btn-outline move-btn" href="#">Find a Room</a>
</section>

<footer class="site-footer">
  <div class="footer-col" style="left:87px">
    <h4>Contact Us</h4>
    <div class="phone">555 - 204 - 8816</div>
    <div class="small">hello@lodgivo-example.com</div>
    <div class="small" style="margin-top:16px">48 Harbour Crest Avenue<br>Dunmore, MI 33590</div>
    <a class="directions" href="#">Get &amp; Directions</a>
  </div>
  <div class="socials">
    <span class="social"></span><span class="social active"></span><span class="social"></span><span class="social"></span>
  </div>
  <div class="footer-col links" style="left:399px">
    <h4 style="margin-bottom:8px">Quick Links</h4>
    <a href="#">Home</a>
    <a class="active" href="#">About Us</a>
    <a href="#">Services</a>
    <a href="#">Portfolio</a>
    <a href="#">Testimonials</a>
    <a href="#">News</a>
    <a href="#">Contact Us</a>
  </div>
  <div class="footer-col" style="left:615px"><h4>How Can We Help?</h4></div>
  <div class="field" style="left:615px;top:119px;width:241px;height:32px">Name</div>
  <div class="field" style="left:873px;top:119px;width:238px;height:32px">Phone</div>
  <div class="field" style="left:615px;top:168px;width:496px;height:31px">Email</div>
  <div class="field" style="left:615px;top:216px;width:496px;height:72px">Message</div>
  <a class="send" href="#"><svg width="12" height="10" viewBox="0 0 12 10"><path d="M0 0l12 5-12 5 2-5z" fill="#fff"/></svg>Send</a>
  <div class="copyright">© 2019 <span class="accent">Lodgivo</span>. All rights reserved.</div>
  <svg class="to-top" width="18" height="22" viewBox="0 0 18 22"><path d="M9 0l9 22-9-6-9 6z" fill="#3276b5"/></svg>
</footer>

</body>
</html>
```